Luxury Wine Label for New Startup Winery

We need a wine label for our new winery startup. We have worked with a local designer but do not feel the resulting label / logo have the elevation required to present our brand as a luxury wine. Our winery is called "Quailbrook Vineyards" and we are focused on extremely high quality hand crafted artisan and estate wines from the Pacific Northwest.
We would like to see designs that utilize a tree line, or other imagery that represents the "Quailbrook" part of our company name. Another interesting feature could be wood grain.
A logo will be required based on your design so please design with this in mind:
This logo should be consistent with the wine bottle label design, and should be representative of our high end exclusive wine while giving a sense of place (Oregon/ Pacific Northwest.)
I will supply an image of the design we received from our local designer, PLEASE NOTE: in general we do like wood grain and tree line concepts but feel the execution was poorly done.
ATTN: Logo design should be suitable for use on: Bottles (Red wine/rose/white wine), Bussiness cards, vehicle signage, business signage, etc
P.S.:
If you have a design that is not outside the box we are still interested in seeing it.
Label is for a burgundy style bottle with a label height of 3.5 - 4" and a width of 3.5-4"
any label <= 4"x4" and >=3.5"x3.5" will be acceptable:
HOWEVER Width should be greater than or equal to height due to the bottle format
Target Market(s)
Wine enthusiasts with adequate discretionary budgets to afford $100 bottles of wine.
Industry/Entity Type
Wine / Winery
Requirements
Must have
- A sense of luxury, a feel of exclusivity, and a theme consistent with our product and brand name
Nice to have
- Tree line, wood grain or other wood themes. Serif fonts
Should not have
- anything cheesy, off topic, hard to read script fonts or anything that makes the label hard to read from a few feet away or too busy

```html
<!DOCTYPE html>
<html lang="en">
<head>
<meta charset="utf-8">
<title>Quailbrook Vineyards — Wine Labels</title>
<link rel="stylesheet" href="https://fonts.googleapis.com/css2?family=Cormorant+Garamond:wght@500;600&display=swap">
<style>
  :root {
    --night: #050505;
    --label-black: #141414;
    --band-black: #1c1c1c;
    --gold: #c9a065;
    --gold-bright: #e8c38a;
    --gold-deep: #8a6a3c;
    --chard-gold: #9c844c;
    --chard-gold-deep: #6f5c32;
    --silver: #b9bcc2;
    --ink: #2a2418;
  }
  * { box-sizing: border-box; margin: 0; padding: 0; }
  html, body { width: 1000px; height: 1200px; overflow: hidden; background: var(--night); }
  .canvas {
    position: relative;
    width: 1000px;
    height: 1200px;
    background: var(--night);
    font-family: "Cormorant Garamond", Georgia, serif;
  }
  .brand-mark {
    position: absolute;
    top: 64px;
    left: 80px;
    display: flex;
    align-items: center;
    gap: 14px;
    color: var(--gold-deep);
    font-size: 22px;
    font-weight: 600;
    letter-spacing: 0.18em;
    text-transform: uppercase;
  }
  .brand-mark .dot {
    width: 44px; height: 44px;
    border: 2px solid var(--gold-deep);
    border-radius: 50%;
  }
  .label-row {
    position: absolute;
    top: 300px;
    left: 60px;
    right: 60px;
    display: flex;
    justify-content: space-between;
  }
  .label {
    position: relative;
    width: 420px;
    height: 400px;
    overflow: hidden;
    text-align: center;
  }
  .label--merlot { background: var(--label-black); }
  .label--chardonnay {
    background: linear-gradient(180deg, var(--chard-gold) 0%, var(--chard-gold-deep) 38%, var(--label-black) 62%, var(--label-black) 100%);
  }
  .label-name {
    padding-top: 44px;
    font-size: 34px;
    font-weight: 600;
    letter-spacing: 0.16em;
    line-height: 1;
  }
  .label-sub {
    margin-top: 8px;
    font-size: 15px;
    font-weight: 600;
    letter-spacing: 0.42em;
    line-height: 1;
  }
  .label--merlot .label-name { color: var(--gold-bright); }
  .label--merlot .label-sub { color: var(--gold); }
  .label--chardonnay .label-name { color: #f2dcae; }
  .label--chardonnay .label-sub { color: #ead3a2; }
  .treeline {
    position: absolute;
    left: 0; right: 0;
    top: 128px;
    height: 90px;
  }
  .label--merlot .treeline {
    background: linear-gradient(180deg, rgba(232,195,138,0) 0%, var(--gold) 55%, var(--gold-deep) 100%);
  }
  .label--chardonnay .treeline {
    background: linear-gradient(180deg, rgba(242,220,174,0) 0%, #e9c791 55%, var(--gold) 100%);
  }
  .variety-band {
    position: absolute;
    left: 0; right: 0;
    top: 218px;
    height: 64px;
    background: var(--band-black);
    display: flex;
    align-items: center;
    justify-content: center;
    font-size: 24px;
    font-weight: 500;
    letter-spacing: 0.2em;
  }
  .label--merlot .variety-band { color: var(--silver); }
  .label--chardonnay .variety-band { color: var(--gold-deep); }
  .woodgrain {
    position: absolute;
    left: 0; right: 0;
    top: 282px;
    height: 118px;
    background: linear-gradient(180deg, var(--gold-deep) 0%, var(--ink) 45%, var(--gold) 80%, var(--gold-deep) 100%);
  }
  .label--chardonnay .woodgrain {
    background: linear-gradient(180deg, var(--gold) 0%, var(--chard-gold-deep) 45%, var(--label-black) 65%, var(--gold-bright) 100%);
  }
</style>
</head>
<body>
<main class="canvas">
  <div class="brand-mark">
    <span class="dot"></span>
    <span>Quailbrook Vineyards</span>
  </div>

  <section class="label-row">
    <article class="label label--merlot">
      <h1 class="label-name">QUAILBROOK</h1>
      <p class="label-sub">VINEYARDS</p>
      <div class="treeline" role="img" aria-label="Gold foil tree line of evergreens over rolling hills"></div>
      <p class="variety-band">MERLOT</p>
      <div class="woodgrain" role="img" aria-label="Gold foil wood grain strata with torn mountain edges"></div>
    </article>

    <article class="label label--chardonnay">
      <h1 class="label-name">QUAILBROOK</h1>
      <p class="label-sub">VINEYARDS</p>
      <div class="treeline" role="img" aria-label="Gold foil tree line of evergreens over rolling hills"></div>
      <p class="variety-band">CHARDONNAY</p>
      <div class="woodgrain" role="img" aria-label="Gold foil wood grain strata with torn mountain edges"></div>
    </article>
  </section>
</main>
</body>
</html>
```